Create a business promotion flyer to leave in customer mailboxes. We are a bulk petroleum supplier, servicing any industry that requires diesel. Base in griffith NSW, servicing griffith area and surrounds.

Business Name - Terra Diesel
Fuel@terradiesel-example.com.au
Owen - 0491 570 362 ohartley@terradiesel-example.com.au
Liam - 0491 570 718 lprosser@terradiesel-example.com.au
Simon - 0491 570 905 skenway@terradiesel-example.com.au
Office 02 5550 1734

Bulk Fuel deliveries.
Oils & lubricants
Local Family owned business

```html
<!DOCTYPE html>
<html lang="en">
<head>
<meta charset="utf-8">
<title>Terra Diesel – Bulk Fuel Deliveries Flyer</title>
<link rel="stylesheet" href="https://fonts.googleapis.com/css2?family=Montserrat:wght@800;900&family=Exo+2:ital,wght@1,500&family=Poppins:wght@500;600&family=Barlow+Condensed:wght@500;600;700&display=swap">
<style>
  :root{
    --red:#e8322a;
    --red-deep:#c9231d;
    --ink:#2f2f31;
    --ink-dark:#1f1f21;
    --grey-ring:#5f5f61;
    --grey-text:#55575a;
    --page:#ffffff;
    --surround:#a7a8aa;
    --photo-light:#e9eaeb;
    --photo-mid:#cfd1d3;
  }
  *{margin:0;padding:0;box-sizing:border-box}
  html,body{width:980px;height:1200px;overflow:hidden;background:var(--surround)}
  .flyer{position:absolute;left:88px;top:83px;width:815px;height:1054px;background:var(--page);overflow:hidden}
  .backdrop-photo{position:absolute;left:0;top:0;width:815px;height:560px;
    background:linear-gradient(180deg,var(--photo-light) 0%,var(--photo-mid) 60%,var(--page) 100%)}
  .hero-ring{position:absolute;left:82px;top:8px;width:652px;height:652px;border-radius:50%;background:var(--grey-ring)}
  .hero-gap{position:absolute;left:92px;top:18px;width:632px;height:632px;border-radius:50%;background:var(--page)}
  .hero-disc{position:absolute;left:108px;top:34px;width:600px;height:600px;border-radius:50%;
    background:radial-gradient(circle at 50% 45%,var(--red) 0%,var(--red) 60%,var(--red-deep) 100%)}
  .brand-tab{position:absolute;left:304px;top:0;width:208px;height:196px;background:linear-gradient(180deg,#fff 0%,#f1f1f1 100%);
    border:1px solid #8a8a8a;border-top:none;border-radius:0 0 104px 104px;
    display:flex;align-items:center;justify-content:center;padding-bottom:30px}
  .brand-tab .brand-name{font-family:'Poppins',sans-serif;font-weight:600;font-size:27px;color:var(--red);line-height:1}
  .headline{position:absolute;left:0;width:815px;text-align:center;color:#fff}
  .headline .title{font-family:'Montserrat',sans-serif;font-weight:900;font-size:62px;letter-spacing:1px;top:292px;line-height:1}
  .headline.sub{font-family:'Exo 2',sans-serif;font-style:italic;font-weight:500;font-size:34px;top:296px}
  .headline.tag{font-family:'Exo 2',sans-serif;font-style:italic;font-weight:500;font-size:21px;top:335px}
  .title-wrap{top:222px}
  .promises{position:absolute;top:378px;left:0;width:815px;display:flex;justify-content:center;gap:24px;
    font-family:'Montserrat',sans-serif;font-weight:800;color:#fff;font-size:0}
  .promise{display:flex;align-items:center;gap:6px;font-family:'Poppins',sans-serif;font-weight:500;font-size:21px;letter-spacing:.3px}
  .promise svg{width:21px;height:21px}
  .truck-photo{position:absolute;left:0;top:436px;width:815px;height:336px;
    background:linear-gradient(180deg,#b9bec4 0%,#dfe2e5 45%,#f4f4f4 75%,#ffffff 100%)}
  .services-title{position:absolute;left:59px;top:700px;line-height:1}
  .services-title .lead{display:block;font-family:'Poppins',sans-serif;font-weight:600;font-size:34px;color:var(--red);letter-spacing:-.5px}
  .services-title .main{display:block;font-family:'Montserrat',sans-serif;font-weight:900;font-size:44px;color:var(--ink);margin-top:6px}
  .service-list{position:absolute;left:57px;top:790px;list-style:none}
  .service-list li{display:flex;align-items:center;gap:10px;height:41px;font-family:'Poppins',sans-serif;font-weight:600;font-size:21px;color:var(--ink)}
  .service-list .dot{width:32px;height:32px;border-radius:50%;background:var(--red);flex:none}
  .base-badge{position:absolute;left:422px;top:723px;width:186px;height:186px;border-radius:50%;background:var(--red);padding:4px}
  .base-badge .inner{width:100%;height:100%;border-radius:50%;background:var(--grey-ring);padding:3px}
  .base-badge .map{width:100%;height:100%;border-radius:50%;background:radial-gradient(circle,#f3f3f3 0%,#dedede 100%);
    display:flex;flex-direction:column;align-items:center;padding-top:30px;line-height:1;font-family:'Barlow Condensed',sans-serif;font-weight:700}
  .base-badge .based{font-size:21px;color:var(--red)}
  .base-badge .town{font-size:34px;color:var(--red);margin-top:2px}
  .base-badge .state{font-size:28px;color:var(--grey-text);margin-top:2px;font-weight:600}
  .base-badge svg{margin-top:6px}
  .delivery-icon{position:absolute;left:622px;top:733px}
  .coverage{position:absolute;left:624px;top:814px;font-family:'Barlow Condensed',sans-serif;font-weight:700;font-size:24px;line-height:27px;color:var(--grey-text);letter-spacing:.5px}
  .contact-bar{position:absolute;left:37px;top:946px;width:741px;height:39px}
  .contact-bar .band{position:absolute;inset:0;background:var(--ink);transform:skewX(-20deg)}
  .contact-bar .slash{position:absolute;top:1px;width:7px;height:28px;background:var(--red);transform:skewX(-20deg)}
  .contact-bar .slash.left{left:-3px}
  .contact-bar .slash.right{right:-3px}
  .contacts{position:absolute;inset:0;display:flex}
  .contact{flex:1;display:flex;align-items:center;justify-content:center;gap:7px;font-family:'Barlow Condensed',sans-serif;font-weight:600;font-size:21px;color:#fff;letter-spacing:.3px}
  .contact.mid{background:var(--ink-dark);border-left:2px solid #777;border-right:2px solid #777}
  .email-line{position:absolute;left:0;top:1000px;width:815px;display:flex;align-items:center;justify-content:center;gap:10px;
    font-family:'Barlow Condensed',sans-serif;font-weight:600;font-size:19px;letter-spacing:6px;color:var(--ink)}
  .email-line .rule{width:40px;height:2px;background:var(--red)}
</style>
</head>
<body>
<main class="flyer">
  <div class="backdrop-photo" role="img" aria-label="Faded aerial photo of a fuel terminal with storage tanks"></div>
  <div class="hero-ring"></div>
  <div class="hero-gap"></div>
  <div class="hero-disc" role="img" aria-label="Red-tinted photo of refinery pipework"></div>

  <div class="brand-tab"><span class="brand-name">Terra Diesel</span></div>

  <div class="headline title-wrap"><h1 class="title">TERRA DIESEL</h1></div>
  <p class="headline sub" style="top:295px">Bulk petroleum supplier</p>
  <p class="headline tag">Your Diesel Supply Partner</p>

  <div class="promises">
    <span class="promise"><svg viewBox="0 0 20 20"><circle cx="10" cy="10" r="10" fill="#fff"/><path d="M5.5 10.2l3 3 6-6.2" stroke="#e8322a" stroke-width="2.4" fill="none" stroke-linecap="round" stroke-linejoin="round"/></svg>RELIABLE</span>
    <span class="promise"><svg viewBox="0 0 20 20"><circle cx="10" cy="10" r="10" fill="#fff"/><path d="M5.5 10.2l3 3 6-6.2" stroke="#e8322a" stroke-width="2.4" fill="none" stroke-linecap="round" stroke-linejoin="round"/></svg>LOCAL</span>
    <span class="promise"><svg viewBox="0 0 20 20"><circle cx="10" cy="10" r="10" fill="#fff"/><path d="M5.5 10.2l3 3 6-6.2" stroke="#e8322a" stroke-width="2.4" fill="none" stroke-linecap="round" stroke-linejoin="round"/></svg>READY TO DELIVER</span>
  </div>

  <div class="truck-photo" role="img" aria-label="Photo of a white road-train fuel tanker parked in front of a depot shed"></div>

  <h2 class="services-title"><span class="lead">BULK FUEL</span><span class="main">DELIVERIES</span></h2>
  <ul class="service-list">
    <li><span class="dot" role="img" aria-label="Fuel nozzle icon"></span>Oils &amp; lubricants</li>
    <li><span class="dot" role="img" aria-label="Tanker icon"></span>Petrol deliveries</li>
    <li><span class="dot" role="img" aria-label="Family owned badge"></span>Local Family owned business</li>
  </ul>

  <div class="base-badge">
    <div class="inner">
      <div class="map" role="img" aria-label="Light grey map of southern New South Wales">
        <span class="based">BASED IN</span>
        <span class="town">GRIFFITH</span>
        <span class="state">NSW</span>
        <svg width="24" height="32" viewBox="0 0 24 32"><path d="M12 31C12 31 2 18 2 11a10 10 0 0 1 20 0c0 7-10 20-10 20z" fill="#e8322a"/><circle cx="12" cy="11" r="4" fill="#fff"/></svg>
      </div>
    </div>
  </div>

  <svg class="delivery-icon" width="92" height="76" viewBox="0 0 92 76">
    <path d="M48 4a34 34 0 0 1 22 58" stroke="#2f2f31" stroke-width="2.5" fill="none"/>
    <path d="M30 10a30 30 0 0 1 40 4 36 36 0 0 1 0 52" stroke="#e8322a" stroke-width="2.5" fill="none"/>
    <g stroke="#2f2f31" stroke-width="2.5" fill="none" stroke-linejoin="round">
      <rect x="26" y="26" width="46" height="30"/>
      <path d="M26 34H12l-8 10v12h22"/>
      <rect x="8" y="38" width="10" height="6"/>
      <circle cx="15" cy="59" r="4" fill="#fff"/><circle cx="50" cy="59" r="4" fill="#fff"/><circle cx="62" cy="59" r="4" fill="#fff"/>
    </g>
  </svg>
  <p class="coverage">SERVICING<br>GRIFFITH AREA<br>&amp; SURROUNDS</p>

  <div class="contact-bar">
    <div class="band"></div>
    <span class="slash left"></span><span class="slash right"></span>
    <div class="contacts">
      <span class="contact"><svg width="18" height="18" viewBox="0 0 24 24" fill="none" stroke="#fff" stroke-width="1.8"><path d="M5 3h4l2 5-3 2a12 12 0 0 0 6 6l2-3 5 2v4a2 2 0 0 1-2 2A18 18 0 0 1 3 5a2 2 0 0 1 2-2z"/></svg>Owen - 0491 570 362</span>
      <span class="contact mid"><svg width="18" height="18" viewBox="0 0 24 24" fill="none" stroke="#fff" stroke-width="1.8"><path d="M5 3h4l2 5-3 2a12 12 0 0 0 6 6l2-3 5 2v4a2 2 0 0 1-2 2A18 18 0 0 1 3 5a2 2 0 0 1 2-2z"/></svg>Liam - 0491 570 718</span>
      <span class="contact"><svg width="18" height="18" viewBox="0 0 24 24" fill="none" stroke="#fff" stroke-width="1.8"><path d="M5 3h4l2 5-3 2a12 12 0 0 0 6 6l2-3 5 2v4a2 2 0 0 1-2 2A18 18 0 0 1 3 5a2 2 0 0 1 2-2z"/></svg>Simon - 0491 570 905</span>
    </div>
  </div>

  <p class="email-line"><span class="rule"></span>FUEL@TERRADIESEL-EXAMPLE.COM.AU<span class="rule"></span></p>
</main>
</body>
</html>
```